Employee Benefits and Insurance Consulting

We are an existing company with over 30 years experience but are changing our name. We would like a simple design with grey tones.

Industry/Entity Type

Insurance

Contact Information for Business Card

Marlow Benefits Consulting
Gerald P Hollins CEO
5172 Brackenridge Road
Fernvale, TN 38442
gerald@marlowbenefits-example.com
555-412-5593 - O
555-247-3861 - C

```html
<!DOCTYPE html>
<html lang="en">
<head>
<meta charset="utf-8">
<title>Marlow Benefits Consulting – Business Card</title>
<link rel="stylesheet" href="https://fonts.googleapis.com/css2?family=Open+Sans:wght@400;600&display=swap">
<style>
  :root {
    --stage: #000000;
    --card-light: #f3f3f3;
    --teal: #1f9189;
    --teal-deep: #16716b;
    --teal-text: #1d8c85;
    --ink: #222222;
    --grey: #6b6b6b;
    --rule: #b9b9b9;
  }
  * { margin: 0; padding: 0; box-sizing: border-box; }
  html, body { width: 1200px; height: 900px; overflow: hidden; background: var(--stage); }
  body { font-family: "Open Sans", Arial, sans-serif; position: relative; }

  .card { position: absolute; top: 200px; width: 310px; height: 502px; }
  .card-front { left: 274px; background: var(--card-light); border-radius: 46px 0 46px 0; }
  .card-back { left: 637px; background: var(--teal); border-radius: 0 46px 0 46px; }

  .brand { position: absolute; left: 0; right: 0; text-align: center; font-weight: 600; text-transform: uppercase; }
  .brand-mark { display: block; width: 44px; height: 44px; margin: 0 auto 26px; }
  .brand-name { display: block; font-size: 24px; letter-spacing: 1.2px; line-height: 1.1; }
  .brand-sub { display: flex; align-items: center; gap: 8px; margin: 3px 26px 0; font-size: 12px; letter-spacing: 3px; line-height: 1.2; }
  .brand-sub::before, .brand-sub::after { content: ""; flex: 1; height: 1px; background: var(--rule); }

  .card-front .brand { top: 52px; color: var(--teal-text); }
  .card-front .brand-mark { background: var(--grey); }
  .card-front .brand-sub { color: var(--grey); }
  .card-back .brand { top: 325px; color: var(--teal-deep); }
  .card-back .brand-mark { background: var(--teal-deep); }
  .card-back .brand-sub::before, .card-back .brand-sub::after { background: var(--teal-deep); }

  .contact { position: absolute; left: 28px; top: 302px; color: var(--ink); font-size: 13px; line-height: 18px; }
  .person-name { color: var(--teal-text); font-size: 18px; font-weight: 600; line-height: 22px; }
  .person-title { margin-bottom: 19px; }
  .address { margin-bottom: 14px; }
  .channels { list-style: none; }
  .channels li { display: flex; align-items: center; height: 21px; }
  .channels svg { width: 10px; height: 10px; margin-right: 11px; fill: var(--teal-text); flex: none; }
</style>
</head>
<body>

<section class="card card-front">
  <div class="brand">
    <span class="brand-mark"></span>
    <span class="brand-name">Marlow Benefits</span>
    <span class="brand-sub">Consulting</span>
  </div>

  <div class="contact">
    <p class="person-name">Gerald P Hollins</p>
    <p class="person-title">CEO</p>
    <p class="address">5172 Brackenridge Road<br>Fernvale, TN 38442</p>
    <ul class="channels">
      <li>
        <svg viewBox="0 0 10 10" aria-hidden="true"><path d="M2 0.5 L3.6 2.6 L2.8 3.6 C3.4 5 4.8 6.4 6.3 7.1 L7.3 6.3 L9.5 7.9 L8.4 9.5 C4.3 9.2 0.7 5.6 0.5 1.5 Z"/></svg>
        555-247-3861
      </li>
      <li>
        <svg viewBox="0 0 10 10" aria-hidden="true"><path d="M2.5 0 H7.5 V10 H2.5 Z M3.4 1.2 V7.6 H6.6 V1.2 Z"/></svg>
        555-412-5593
      </li>
      <li>
        <svg viewBox="0 0 10 10" aria-hidden="true"><path d="M0.5 2 H9.5 V8.5 H0.5 Z M1.3 2.6 L5 5.6 L8.7 2.6 Z" fill-rule="evenodd"/></svg>
        gerald@marlowbenefits-example.com
      </li>
    </ul>
  </div>
</section>

<section class="card card-back">
  <div class="brand">
    <span class="brand-mark"></span>
    <span class="brand-name">Marlow Benefits</span>
    <span class="brand-sub">Consulting</span>
  </div>
</section>

</body>
</html>
```